Pitch Deck Powerpoint Template for Entrepreneurship/Education Based Nonprofit

I need a stylish powerpoint design for a start-up nonprofit called Harbor Venture Works (HVW). I am building HVWs pitch deck to raise money. HVW is an entrepreneurial incubator and accelerator that seeks to identify, validate, test, and launch innovative ventures that improve public education. An example of our model, and one of our partners, is Kestrel Schools in New Orleans and New York :http://kestrelsch.example.org

We need the deck to look sleek and innovative - like a start-up pitch deck. Lots of different templates and fonts that pop off the page.

Target Market(s)

Individuals, foundations, and any other stakeholder - we are pitching a new business model and asking for money.

Industry/Entity Type

Building

Font styles to use
Sans Serif

Requirements
Must have
• A sleek/modern feel with several different template slides. charts and graphs/ strong fonts that pop off the page, use of the logo:
• It would be great to have a slide describing the 3 primary programs at Harbor Venture Works (HVW):
• - HVWspark - come in with an idea for an innovation in education, and we will do a two day workshop to examine your business assumptions and discuss next steps.
• - HVWpropell - take your idea to a prototype and launch to customers - we help you with an intensive 30 day program
• - HVWnurture - for existing nonprofit projects, we allow you to work under our umbrella to launch and build capacity
• Slides: Problem Definition, Solution, Value Proposition, Data/MEasurement, Key Partners, About the founder, Key Advisors

```html
<!DOCTYPE html>
<html lang="en">
<head>
<meta charset="utf-8">
<title>Ask of Money – Harbor Venture Works</title>
<link rel="stylesheet" href="https://fonts.googleapis.com/css2?family=Oswald:wght@500&family=Lato:wght@400;700;900&family=Open+Sans:wght@400&display=swap">
<style>
  :root {
    --board: #000000;
    --paper: #ffffff;
    --navy: #02427a;
    --magenta: #a8208a;
    --stage-purple: #652d8f;
    --stage-green: #5a8e0a;
    --stage-orange: #f15a24;
    --stage-blue: #27a8f5;
    --rail: #b5b5b5;
    --white: #ffffff;
  }
  * { margin: 0; padding: 0; box-sizing: border-box; }
  html, body { width: 1200px; height: 1200px; overflow: hidden; background: var(--board); }
  .board { position: relative; width: 1200px; height: 1200px; background: var(--board); }
  .board-title {
    position: absolute; top: 70px; left: 0; width: 1200px; text-align: center;
    font-family: "Open Sans", sans-serif; font-weight: 400; font-size: 31px; color: var(--white);
  }
  .slide { position: absolute; left: 35px; top: 168px; width: 1128px; height: 845px; background: var(--paper); overflow: hidden; }
  .slide-header {
    position: absolute; left: 0; top: 48px; width: 807px; height: 102px; background: var(--navy);
  }
  .slide-title {
    position: absolute; left: 37px; top: 23px;
    font-family: "Oswald", sans-serif; font-weight: 500; font-size: 45px; line-height: 56px;
    color: var(--white); letter-spacing: -1.2px;
  }
  .brand {
    position: absolute; left: 838px; top: 52px;
    font-family: "Lato", sans-serif; font-weight: 900; font-size: 35px; line-height: 34px;
    color: var(--navy);
  }
  .timeline { position: absolute; left: 0; top: 0; width: 1128px; height: 845px; }
  .stage { position: absolute; width: 463px; height: 128px; padding: 13px 19px; color: var(--white); }
  .stage-name { font-family: "Oswald", sans-serif; font-weight: 500; font-size: 26px; line-height: 1; letter-spacing: -0.8px; }
  .stage-text { margin-top: 13px; font-family: "Lato", sans-serif; font-size: 17px; line-height: 20.5px; white-space: nowrap; }
  .stage--1 { left: 34px; top: 211px; background: var(--stage-purple); }
  .stage--2 { left: 635px; top: 325px; background: var(--stage-green); }
  .stage--3 { left: 34px; top: 445px; background: var(--stage-orange); }
  .stage--4 { left: 635px; top: 561px; background: var(--stage-blue); }
  .footer-band { position: absolute; left: 0; top: 752px; width: 1128px; height: 93px; background: var(--magenta); }
  .footer-text {
    position: absolute; top: 787px; font-family: "Lato", sans-serif; font-weight: 700;
    font-size: 27px; color: var(--white);
  }
  .footer-page { left: 49px; }
  .footer-url { right: 59px; }
</style>
</head>
<body>
<div class="board">
  <h1 class="board-title">ASK OF MONEY</h1>

  <section class="slide">
    <div class="slide-header"><h2 class="slide-title">ASK OF MONEY</h2></div>
    <div class="brand">Harbor<br>Venture<br>Works</div>

    <svg class="timeline" width="1128" height="845" viewBox="0 0 1128 845" aria-hidden="true">
      <line x1="563" y1="211" x2="563" y2="560" stroke="var(--rail)" stroke-width="2"/>
      <line x1="497" y1="212" x2="563" y2="212" stroke="var(--stage-purple)" stroke-width="2"/>
      <line x1="563" y1="326" x2="635" y2="326" stroke="var(--stage-green)" stroke-width="2"/>
      <line x1="497" y1="446" x2="563" y2="446" stroke="var(--stage-orange)" stroke-width="2"/>
      <line x1="563" y1="562" x2="635" y2="562" stroke="var(--stage-blue)" stroke-width="2"/>
      <circle cx="563" cy="211" r="12.5" fill="var(--stage-purple)"/>
      <circle cx="563" cy="325" r="12.5" fill="var(--stage-green)"/>
      <circle cx="563" cy="445" r="12.5" fill="var(--stage-orange)"/>
      <circle cx="563" cy="560" r="12.5" fill="var(--stage-blue)"/>
    </svg>

    <article class="stage stage--1">
      <h3 class="stage-name">STAGE 1</h3>
      <p class="stage-text">Lorem ipsum dolor sit amet, consectetuer adipiscing<br>elit, sed diam nonummy nibh euismod tincidunt ut lao-<br>reet dolore magna aliquam erat volutpat.</p>
    </article>
    <article class="stage stage--2">
      <h3 class="stage-name">STAGE 2</h3>
      <p class="stage-text">Lorem ipsum dolor sit amet, consectetuer adipiscing<br>elit, sed diam nonummy nibh euismod tincidunt ut lao-<br>reet dolore magna aliquam erat volutpat.</p>
    </article>
    <article class="stage stage--3">
      <h3 class="stage-name">STAGE 3</h3>
      <p class="stage-text">Lorem ipsum dolor sit amet, consectetuer adipiscing<br>elit, sed diam nonummy nibh euismod tincidunt ut lao-<br>reet dolore magna aliquam erat volutpat.</p>
    </article>
    <article class="stage stage--4">
      <h3 class="stage-name">STAGE 4</h3>
      <p class="stage-text">Lorem ipsum dolor sit amet, consectetuer adipiscing<br>elit, sed diam nonummy nibh euismod tincidunt ut lao-<br>reet dolore magna aliquam erat volutpat.</p>
    </article>

    <div class="footer-band"></div>
    <span class="footer-text footer-page">Page 1</span>
    <span class="footer-text footer-url">www.hvw.example.com</span>
  </section>
</div>
</body>
</html>
```